Corporate Business Card

Very professional, Modern, Not to busy, include phone address email, website
(253) 617-4930, 18761 52nd Avenue S, Kent, WA 98047, martin@plumlinegroup.com, varkoworks.com

Target Market(s)

Manufacturing

Industry/Entity Type

Aero, machining, manufacturing, Off road racing

Contact Information for Business Card

Phone, address email, website

```html
<!DOCTYPE html>
<html lang="en">
<head>
<meta charset="utf-8">
<title>Varko Works – Business Card</title>
<link rel="stylesheet" href="https://fonts.googleapis.com/css2?family=Roboto:wght@400;700;900&family=Russo+One&display=swap">
<style>
  :root {
    --bg: #2a2a2a;
    --card: #efefef;
    --navy: #24366b;
    --red: #c4232a;
    --ink: #1f2b55;
  }
  * { margin: 0; padding: 0; box-sizing: border-box; }
  html, body { width: 1200px; height: 1138px; overflow: hidden; }
  body { background: var(--bg); font-family: "Roboto", sans-serif; position: relative; }

  .card {
    position: absolute;
    left: 290px;
    width: 620px;
    height: 374px;
    background: linear-gradient(160deg, #f3f3f3 0%, #e9e9e9 100%);
    border-radius: 14px;
    overflow: hidden;
  }
  .card--front { top: 186px; }
  .card--back { top: 608px; }

  /* Front */
  .brand-name {
    position: absolute;
    font-family: "Roboto", sans-serif;
    font-weight: 900;
    color: var(--navy);
    letter-spacing: 1px;
    white-space: nowrap;
  }
  .card--front .brand-name {
    left: 0; right: 0; top: 118px;
    text-align: center;
    font-size: 70px;
  }
  .front-web {
    position: absolute;
    left: 0; right: 0; top: 326px;
    display: flex; align-items: center; justify-content: center; gap: 18px;
    font-size: 17px; color: #222;
  }
  .front-web .flank { width: 70px; height: 3px; background: var(--red); border-radius: 2px; }
  .front-web .flank--left { clip-path: polygon(0 50%, 100% 0, 100% 100%); }
  .front-web .flank--right { clip-path: polygon(0 0, 100% 50%, 0 100%); }
  .stripe {
    position: absolute; left: 0; right: 0; bottom: 0; height: 9px;
    background: linear-gradient(90deg, var(--navy) 0 50%, var(--red) 50% 100%);
  }

  /* Back */
  .card--back .brand-name {
    left: 44px; top: 74px;
    font-size: 36px;
  }
  .person {
    position: absolute; right: 48px; top: 78px;
    font-family: "Russo One", sans-serif;
    font-size: 23px; letter-spacing: 0.5px;
  }
  .person .first { color: var(--navy); }
  .person .last { color: var(--red); }

  .contact-list {
    position: absolute; right: 48px; top: 230px;
    list-style: none;
  }
  .contact-list li {
    display: flex; align-items: center; justify-content: flex-end;
    gap: 14px; height: 24.5px;
    font-size: 16.5px; color: var(--ink);
  }
  .contact-list .accent { color: var(--red); }
  .contact-list svg { width: 16px; height: 16px; fill: var(--red); flex: none; }
</style>
</head>
<body>

<section class="card card--front">
  <div class="brand-name">VARKO WORKS</div>
  <div class="front-web">
    <span class="flank flank--left"></span>
    <span>www.varkoworks.com</span>
    <span class="flank flank--right"></span>
  </div>
  <div class="stripe"></div>
</section>

<section class="card card--back">
  <div class="brand-name">VARKO WORKS</div>
  <div class="person"><span class="first">MARTIN</span> <span class="last">KELLER</span></div>

  <ul class="contact-list">
    <li>(253) 617-4930
      <svg viewBox="0 0 16 16" aria-hidden="true"><path d="M2 6c0-2 3-3 6-3s6 1 6 3v1h-3V5.5C10 5 9 5 8 5s-2 0-3 .5V7H2zM4 8h8l2 5H2z"/></svg>
    </li>
    <li>martin@plumlinegroup.com
      <svg viewBox="0 0 16 16" aria-hidden="true"><path d="M1 3h14v10H1zM2.5 4.5 8 9l5.5-4.5v1.6L8 10.5 2.5 6.1z" fill-rule="evenodd"/></svg>
    </li>
    <li><span>www.<span class="accent">varkoworks</span>.com</span>
      <svg viewBox="0 0 16 16" aria-hidden="true"><path d="M8 1a7 7 0 1 0 0 14A7 7 0 0 0 8 1zm0 1.5c.8 0 1.7 1.6 2 4H6c.3-2.4 1.2-4 2-4zM2.6 7.3h2.6a13 13 0 0 0 0 1.4H2.6a5.5 5.5 0 0 1 0-1.4zm8.2 0h2.6a5.5 5.5 0 0 1 0 1.4h-2.6a13 13 0 0 0 0-1.4zM6 9.5h4c-.3 2.4-1.2 4-2 4s-1.7-1.6-2-4zM6.4 7.3h3.2a11 11 0 0 1 0 1.4H6.4a11 11 0 0 1 0-1.4z"/></svg>
    </li>
    <li>18761 52nd Avenue S, Kent, WA 98047
      <svg viewBox="0 0 16 16" aria-hidden="true"><path d="M8 1a5 5 0 0 0-5 5c0 3.5 5 9 5 9s5-5.5 5-9a5 5 0 0 0-5-5zm0 3a2 2 0 1 1 0 4 2 2 0 0 1 0-4z" fill-rule="evenodd"/></svg>
    </li>
  </ul>
</section>

</body>
</html>
```